TalkHarbor - Language Coaching Services

Sleek, innovative, trendy design for Language Coaching business.

TalkHarbor is a new UK based company that provides Language Coaching services. We offer highly personalized on-line and face to face language courses. We also impart learning techniques workshops based on the latest neuroscience research for second-language acquisition.

Target Market(s)

See attached info

Industry/Entity Type

Consulting

Contact Information for Business Card

TalkHarbor
DaniaKV@talkharbor.co.uk
TalkHarbor.co.uk
London, UK

Font styles to use
Sans Serif

```html
<!DOCTYPE html>
<html lang="en">
<head>
<meta charset="utf-8">
<title>TalkHarbor Business Card</title>
<link rel="stylesheet" href="https://fonts.googleapis.com/css2?family=Montserrat:wght@400;600&family=Lato:wght@400&display=swap">
<style>
  :root {
    --backdrop: #e9e4dc;
    --kraft-light: #d8b487;
    --kraft-mid: #c99c6b;
    --kraft-dark: #b88a58;
    --ink: #141210;
  }
  html, body {
    margin: 0;
    padding: 0;
    width: 1200px;
    height: 900px;
    overflow: hidden;
    background: var(--backdrop);
  }
  .canvas {
    position: relative;
    width: 1200px;
    height: 900px;
  }
  .card {
    position: absolute;
    left: 330px;
    width: 556px;
    height: 342px;
    background: radial-gradient(ellipse at 45% 10%, var(--kraft-light) 0%, var(--kraft-mid) 55%, var(--kraft-dark) 100%);
    color: var(--ink);
    box-shadow: 0 2px 6px rgba(0,0,0,0.25);
  }
  .card--front { top: 90px; }
  .card--back { top: 470px; }

  .front-content {
    position: absolute;
    left: 0; right: 0; top: 80px;
    text-align: center;
    font-family: "Lato", sans-serif;
    font-size: 16px;
    line-height: 20px;
  }
  .holder-name {
    font-family: "Montserrat", sans-serif;
    font-weight: 600;
    font-size: 21px;
    letter-spacing: 0.5px;
    line-height: 24px;
    margin: 0;
  }
  .holder-role { margin: 0 0 11px; }
  .rule {
    width: 178px;
    height: 1px;
    background: var(--ink);
    margin: 0 auto 8px;
  }
  .company { margin: 0; }
  .contact-icons {
    display: flex;
    align-items: center;
    justify-content: center;
    gap: 4px;
    margin: 10px 0 9px;
  }
  .contact-icons .line {
    width: 52px;
    height: 1px;
    background: var(--ink);
    margin: 0 2px;
  }
  .contact-icons svg { display: block; }
  .contact-list { margin: 0; }

  .brand {
    position: absolute;
    left: 0; right: 0; top: 86px;
    display: flex;
    flex-direction: column;
    align-items: center;
  }
  .brand-circle {
    width: 112px;
    height: 112px;
    border: 6px solid var(--ink);
    border-radius: 50%;
    box-sizing: border-box;
  }
  .brand-name {
    margin-top: 12px;
    font-family: "Montserrat", sans-serif;
    font-weight: 400;
    font-size: 44px;
    letter-spacing: 1px;
    line-height: 50px;
  }
</style>
</head>
<body>
<div class="canvas">
  <section class="card card--front">
    <div class="front-content">
      <p class="holder-name">MARCUS HALE</p>
      <p class="holder-role">Managing Director</p>
      <div class="rule"></div>
      <p class="company">TALKHARBOR<br>London, UK</p>
      <div class="contact-icons">
        <span class="line"></span>
        <svg width="17" height="17" viewBox="0 0 17 17" aria-label="Phone">
          <rect width="17" height="17" fill="#141210"/>
          <path d="M4 6 q4.5-3 9 0 v1.5 h-2.5 v-1 q-2-0.8-4 0 v1 H4z M5.5 8.5 h6 l1 4 h-8z" fill="#d2ad80"/>
        </svg>
        <svg width="17" height="17" viewBox="0 0 17 17" aria-label="Email">
          <rect width="17" height="17" fill="#141210"/>
          <rect x="3" y="5" width="11" height="7.5" fill="none" stroke="#d2ad80" stroke-width="1.2"/>
          <path d="M3 5 l5.5 4.5 L14 5" fill="none" stroke="#d2ad80" stroke-width="1.2"/>
        </svg>
        <svg width="17" height="17" viewBox="0 0 17 17" aria-label="Website">
          <rect width="17" height="17" fill="#141210"/>
          <circle cx="8.5" cy="8.5" r="5" fill="none" stroke="#d2ad80" stroke-width="1.2"/>
          <path d="M3.5 8.5 h10 M8.5 3.5 q-3 5 0 10 q3-5 0-10" fill="none" stroke="#d2ad80" stroke-width="1"/>
        </svg>
        <span class="line"></span>
      </div>
      <p class="contact-list">044 777 5555<br>DaniaKV@talkharbor.co.uk<br>www.TalkHarbor.co.uk</p>
    </div>
  </section>

  <section class="card card--back">
    <div class="brand">
      <div class="brand-circle"></div>
      <div class="brand-name">TALKHARBOR</div>
    </div>
  </section>
</div>
</body>
</html>
```